Window company.

Hello,

We are a small family business located in Madrid, Spain that works nationwide to fix, change or mount the windows of your home / premises.

The group of possible clients to whom the flyer is focused ranges from 30 to 65 years, families in general who want comfort at home and extra savings every year in heating.

It must include not only graphics and a striking aesthetic in accordance with the concepts of wanting to reach / transmit the final product to the customer to sell the product.

Details to also include:

-Brief history of the company and its foundation in 2006. It will be subsequently translated into Spanish so put in words what you consider necessary so that the client stays with the concept that we are professionals.

--Specialized in exterior aluminum and PVC carpentry.

-We move to your home for a first visit and we provide the budget totally free without any commitment.

- Also payment facilities; up to 3 times, without interest.

-Contact details of the company. (WhatsApp, email, phone and location)
Open: Mon - Friday 11,00am - 9pm
Saturday: 12,00am - 7pm
Sunday: Closed

Also as a suggestion, to decide on your own, graphics of types of window openings, if you consider that anything that is striking for the client so it wonr be yet another advertising flyer.

We are open to all kinds of ideas, all of them involving marketing branding.

We are open to any type of idea and we want to stand out, the construction world is tough and we have an idea to grow, taking into account that it must not only be beautiful but commercial to attract potential customers with all kinds of purchasing power.

Thank you.

```html
<!DOCTYPE html>
<html lang="es">
<head>
<meta charset="utf-8">
<title>Ventara – Carpintería de aluminio y PVC</title>
<link href="https://fonts.googleapis.com/css2?family=Oswald:wght@400;500;600&family=Open+Sans:wght@400;600;700&display=swap" rel="stylesheet">
<style>
  :root{
    --red:#c8342b;
    --red-dark:#a92a22;
    --ink:#2b2b2b;
    --grey-text:#4a4a4a;
    --light:#efefef;
    --panel:#6b6e72;
    --footer:#8d8f93;
    --white:#ffffff;
  }
  *{margin:0;padding:0;box-sizing:border-box}
  html,body{width:848px;height:1200px;overflow:hidden;background:var(--white)}
  .flyer{position:relative;width:848px;height:1200px;overflow:hidden;background:var(--white);font-family:"Open Sans",Arial,sans-serif;color:var(--ink)}

  .brand{position:absolute;left:40px;top:62px;display:flex;align-items:center;gap:14px}
  .brand-mark{width:26px;height:26px;background:var(--red)}
  .brand-name{font-family:"Open Sans",Arial,sans-serif;font-weight:600;font-size:36px;letter-spacing:2px;color:#8a8a8a}

  .social{position:absolute;right:44px;top:38px;display:flex;gap:19px}
  .social span{width:38px;height:38px;border:1.5px solid #9a9a9a;border-radius:50%}

  .hero{position:absolute;left:0;top:138px;width:848px;height:374px;background:linear-gradient(180deg,#ffffff 0%,#f4f4f4 100%)}
  .hero-rule{position:absolute;left:0;top:0;width:848px;height:3px;background:var(--red)}
  .hero-photo{position:absolute;right:0;top:3px;width:480px;height:371px;
    background:linear-gradient(90deg,rgba(255,255,255,1) 0%,rgba(236,226,218,.6) 18%,#d9c4b6 45%,#c9b0a2 70%,#e6dcd6 100%)}
  .headline{position:absolute;left:35px;top:60px;font-family:"Oswald",Arial,sans-serif;font-weight:500;font-size:44px;line-height:50px;color:var(--ink);letter-spacing:.5px}
  .ribbon{position:absolute;left:0;top:225px;width:398px;height:52px;background:var(--red);clip-path:polygon(0 0,100% 0,96% 100%,0 100%);
    font-family:"Oswald",Arial,sans-serif;font-size:29px;color:var(--white);padding-left:37px;line-height:52px}
  .guarantee{position:absolute;left:37px;top:290px;font-family:"Oswald",Arial,sans-serif;font-weight:500;font-size:28px;color:var(--ink)}

  .about{position:absolute;left:0;top:512px;width:848px;height:214px;background:linear-gradient(180deg,#e4e4e4,#f7f7f7)}
  .about-left{position:absolute;left:35px;top:40px;width:370px}
  .about-title{font-family:"Open Sans",Arial,sans-serif;font-weight:700;font-size:20px;color:var(--red);margin-bottom:12px}
  .about p{font-size:15px;line-height:21px;color:var(--grey-text);text-align:justify}
  .about-divider{position:absolute;left:423px;top:36px;width:1.5px;height:164px;background:#9a9a9a}
  .about-right{position:absolute;left:445px;top:40px;width:387px}
  .about-right h3{font-size:14.5px;font-weight:700;line-height:19px;color:var(--ink);margin-bottom:8px}
  .pay-tag{position:absolute;left:445px;top:167px;width:387px;height:34px;background:var(--red);color:var(--white);
    font-family:"Oswald",Arial,sans-serif;font-size:15.5px;text-align:center;line-height:34px}

  .services{position:absolute;left:0;top:762px;width:848px;height:241px;background:linear-gradient(180deg,#7b7e82 0%,#5e6165 100%)}
  .services::after{content:"";position:absolute;left:0;bottom:0;width:100%;height:3px;background:var(--red)}
  .services-rule{position:absolute;left:0;top:-2px;width:848px;height:3px;background:var(--red)}
  .services-tab{position:absolute;left:0;top:736px;width:296px;height:40px;background:var(--red);clip-path:polygon(0 0,100% 0,93% 100%,0 100%);
    font-family:"Oswald",Arial,sans-serif;font-size:24px;color:var(--white);padding-left:35px;line-height:40px}
  .service{position:absolute;display:flex;align-items:center;gap:22px;font-family:"Oswald",Arial,sans-serif;font-size:20px;color:var(--white)}
  .service svg{width:42px;height:42px;flex:none}

  .hours{position:absolute;left:0;top:1038px;width:848px;text-align:center;font-family:"Open Sans",Arial,sans-serif;font-size:16px;color:var(--ink)}
  .footer{position:absolute;left:0;top:1122px;width:848px;height:78px;background:var(--footer);color:var(--white);text-align:center;font-size:17px;line-height:25px;padding-top:16px}
  .call{position:absolute;left:78px;top:1092px;width:683px;height:42px;border-radius:21px;background:var(--red);color:var(--white);
    display:flex;align-items:center;justify-content:center;gap:10px;font-family:"Open Sans",Arial,sans-serif;font-weight:700;font-size:18px}
  .call .label{font-family:"Oswald",Arial,sans-serif;font-weight:500;font-size:20px;letter-spacing:.5px;margin-right:6px}
  .call svg{width:18px;height:18px}
</style>
</head>
<body>
<div class="flyer">

  <div class="brand"><span class="brand-mark"></span><span class="brand-name">VENTARA</span></div>
  <div class="social" aria-hidden="true"><span></span><span></span><span></span><span></span></div>

  <section class="hero">
    <div class="hero-photo" role="img" aria-label="Familia sonriente con un niño pequeño en el sofá de casa"></div>
    <div class="hero-rule"></div>
    <h1 class="headline">AHORRE<br>TODOS LOS AÑOS<br>EN CALEFACCIÓN</h1>
    <div class="ribbon">Presupuestos sin compromiso</div>
    <div class="guarantee">CALIDAD GARANTIZADA !</div>
  </section>

  <section class="about">
    <div class="about-left">
      <h2 class="about-title">QUIENES SOMOS</h2>
      <p>Somos una empresa familiar con mas de 20 años de experiencia trabajando a nivel nacional arreglando, montando y cambiando ventanas, persianas, etc.</p>
    </div>
    <div class="about-divider"></div>
    <div class="about-right">
      <h3>ESPECIALIZADOS EN CARPINTERÍA DE ALUMINIO EXTERIOR Y CARPINTERÍA DE PVC.</h3>
      <p>Nos trasladamos a su vivienda para una primera visita y le proporcionamos un presupuesto totalmente gratuito.</p>
    </div>
    <div class="pay-tag">FACILIDADES DE PAGO; HASTA 3 VECES SIN INTERESES</div>
  </section>

  <section class="services" role="img" aria-label="Fachada de una casa de ladrillo con ventanas, en tonos grises">
    <div class="services-rule"></div>
  </section>
  <div class="services-tab">NUESTROS SERVICIOS</div>

  <div class="service" style="left:45px;top:786px">
    <svg viewBox="0 0 42 42"><rect x="1" y="1" width="40" height="40" rx="4" fill="none" stroke="#fff" stroke-width="1.5"/><path d="M9 22 L21 11 L33 22 V32 H9 Z" fill="var(--red)"/></svg>CARPINTERIA DE EXTERIOR</div>
  <div class="service" style="left:45px;top:837px">
    <svg viewBox="0 0 42 42"><rect x="1" y="1" width="40" height="40" rx="4" fill="none" stroke="#fff" stroke-width="1.5"/><path d="M9 12 H33 V18 H9 Z" fill="var(--red)"/><rect x="11" y="20" width="20" height="12" fill="none" stroke="var(--red)" stroke-width="2"/></svg>TOLDOS</div>
  <div class="service" style="left:45px;top:888px">
    <svg viewBox="0 0 42 42"><rect x="1" y="1" width="40" height="40" rx="4" fill="none" stroke="#fff" stroke-width="1.5"/><rect x="11" y="9" width="20" height="24" fill="none" stroke="var(--red)" stroke-width="2.5"/><line x1="21" y1="9" x2="21" y2="33" stroke="var(--red)" stroke-width="2.5"/></svg>ALUMINIO</div>
  <div class="service" style="left:45px;top:940px">
    <svg viewBox="0 0 42 42"><rect x="1" y="1" width="40" height="40" rx="4" fill="none" stroke="#fff" stroke-width="1.5"/><rect x="10" y="10" width="22" height="22" fill="none" stroke="var(--red)" stroke-width="2.5"/><line x1="21" y1="10" x2="21" y2="32" stroke="var(--red)" stroke-width="2"/><line x1="10" y1="21" x2="32" y2="21" stroke="var(--red)" stroke-width="2"/></svg>DOBLE ACRISTALAMIENTO</div>

  <div class="service" style="left:427px;top:786px">
    <svg viewBox="0 0 42 42"><rect x="1" y="1" width="40" height="40" rx="4" fill="none" stroke="#fff" stroke-width="1.5"/><rect x="10" y="10" width="22" height="22" fill="none" stroke="var(--red)" stroke-width="2.5"/><line x1="21" y1="10" x2="21" y2="32" stroke="var(--red)" stroke-width="2"/><line x1="10" y1="21" x2="32" y2="21" stroke="var(--red)" stroke-width="2"/></svg>PVC</div>
  <div class="service" style="left:427px;top:837px">
    <svg viewBox="0 0 42 42"><rect x="1" y="1" width="40" height="40" rx="4" fill="none" stroke="#fff" stroke-width="1.5"/><rect x="10" y="10" width="22" height="22" fill="var(--red)"/></svg>MOSQUITERAS</div>
  <div class="service" style="left:427px;top:888px">
    <svg viewBox="0 0 42 42"><rect x="1" y="1" width="40" height="40" rx="4" fill="none" stroke="#fff" stroke-width="1.5"/><path d="M9 12 L30 10 L33 31 L12 33 Z" fill="var(--red)"/></svg>CERRAMIENTOS</div>
  <div class="service" style="left:427px;top:940px">
    <svg viewBox="0 0 42 42"><rect x="1" y="1" width="40" height="40" rx="4" fill="none" stroke="#fff" stroke-width="1.5"/><path d="M21 12 V30 M12 21 H30" stroke="var(--red)" stroke-width="3"/></svg>Y MUCHO MAS</div>

  <p class="hours">ABIERTO: LUNES - VIERNES 11:00 - 21:00 | SÁBADOS: 12:00 - 18:00 | DOMINGOS: CERRADO</p>

  <footer class="footer">
    <p>presupuestos@ventara-ventanas.es | www.ventara-ventanas.es</p>
    <p>Pol. Ind. Los Olivos 4, Getafe, Spain 28906</p>
  </footer>

  <div class="call">
    <span class="label">LLÁMENOS AL</span>
    <svg viewBox="0 0 24 24"><circle cx="12" cy="12" r="10.5" fill="none" stroke="#fff" stroke-width="2"/><path d="M8.5 7 L10.5 7 L11.3 9.5 L10 10.5 Q11 13 13.5 14 L14.5 12.7 L17 13.5 L17 15.5 Q12 17 8.5 11.5 Z" fill="#fff"/></svg>
    <span>+34 600 41 27 85 para mas información</span>
  </div>

</div>
</body>
</html>
```